Elegant Business Card for Technology Company

Client is a supplier of innovative industrial communications and automation equipment since 2002. This contest is to gather fresh ideas for a redesign of the existing business card. Client is looking for design that best communicates tagline "Industrial Networking and Computing Specialist".

Design submissions should look modern, clean, elegant and professional. It should not be cluttered. Use white as the primary colour. Orange and black as secondary colour. Refer to jpeg File 1 on the current design.

Fonts used by Client used include Arial Regular, Arial Black, Roboto Regular, Roboto Black and Lato.

The winning design will be sent for offset printing using super white 250gsm artcard paper (open for suggestions).

Target Market(s)

System Engineers, Project Managers, Purchasing Managers from companies providing engineering services for Smart Cities.

Industry/Entity Type

Information Technology

Contact Information for Business Card

Refer to PDF File 3 for Business Card Details. Priority of short contact information would be as follows Name > Job Title > Email > Mobile > Web > Tel > Fax > Business Address >UEN (UEN represents company registration number)

Font styles to use
Sans Serif

Colors
ffffff
f37122
000000
5c5c5c

Requirements
Must have
• Refer to AI File 2 (Company Logo) & PDF File 3 (Information on Namecard)
Should not have
• No QR codes
• No Social Media Icons
• Do not create full Black or Orange colour background

```html
<!DOCTYPE html>
<html lang="en">
<head>
<meta charset="utf-8">
<title>Kelvane Business Card</title>
<link href="https://fonts.googleapis.com/css2?family=Lato:wght@400;700;900&display=swap" rel="stylesheet">
<style>
  :root {
    --white: #ffffff;
    --orange: #f37122;
    --black: #000000;
    --grey: #5c5c5c;
    --ink: #1a1a1a;
    --stage: #2b2b2b;
  }
  * { box-sizing: border-box; margin: 0; padding: 0; }
  html, body {
    width: 1200px; height: 1166px; overflow: hidden;
    background: var(--stage);
    font-family: "Lato", sans-serif;
  }
  .sheet {
    position: relative; width: 1200px; height: 1166px;
    display: flex; flex-direction: column; align-items: center;
    justify-content: center; gap: 38px;
  }
  .card {
    position: relative; width: 880px; height: 528px;
    background: var(--white); overflow: hidden;
  }

  /* Brand lockup */
  .brand { display: flex; align-items: center; gap: 22px; }
  .brand-dot { border-radius: 50%; background: var(--orange); flex: none; }
  .brand-name { font-weight: 900; color: var(--black); letter-spacing: 2px; line-height: 1; }

  /* Front */
  .card-front .brand { position: absolute; left: 232px; top: 118px; }
  .card-front .brand-dot { width: 92px; height: 92px; }
  .card-front .brand-name { font-size: 76px; }
  .tagline {
    position: absolute; left: 232px; top: 250px;
    font-weight: 700; font-size: 22px; color: var(--ink);
  }
  .services-band {
    position: absolute; left: 0; right: 0; bottom: 34px; height: 108px;
    background: var(--orange); color: var(--white);
    display: flex; flex-direction: column; justify-content: center;
    padding-left: 88px; font-size: 21px; line-height: 1.4;
  }

  /* Back */
  .card-back .brand { position: absolute; left: 70px; top: 214px; }
  .card-back .brand-dot { width: 110px; height: 110px; }
  .card-back .brand-name { font-size: 70px; }
  .accent-bar {
    position: absolute; right: 22px; top: 0; width: 16px; height: 232px;
    background: var(--orange);
  }
  .contact {
    position: absolute; right: 80px; top: 54px;
    text-align: right; color: var(--ink); font-size: 21px; line-height: 1.3;
  }
  .contact-name { color: var(--orange); font-size: 25px; letter-spacing: 1px; }
  .contact-title { margin-bottom: 6px; }
  .contact-address { margin-bottom: 6px; }
  .contact-line { display: flex; justify-content: flex-end; align-items: center; gap: 10px; }
  .contact-line svg { width: 18px; height: 18px; fill: var(--orange); flex: none; }
  .contact-reg { margin-top: 12px; }
</style>
</head>
<body>
<main class="sheet">

  <section class="card card-front">
    <div class="brand">
      <span class="brand-dot"></span>
      <span class="brand-name">KELVANE</span>
    </div>
    <p class="tagline">Industrial Networking and Computing Specialist</p>
    <div class="services-band">
      <p>Industrial Ethernet / Wireless / Cellular • Industrial and Embedded Computing</p>
      <p>Serial / Fieldbus Connectivity • IP Video Surveillance • Remote Automation</p>
    </div>
  </section>

  <section class="card card-back">
    <div class="accent-bar"></div>
    <div class="brand">
      <span class="brand-dot"></span>
      <span class="brand-name">KELVANE</span>
    </div>
    <div class="contact">
      <p class="contact-name">DANIEL LIM</p>
      <p class="contact-title">Sales manager</p>
      <div class="contact-address">
        <p>Kelvane Asia Pacific Pte Ltd</p>
        <p>24 Harbour Lane</p>
        <p>Harbour Works #05-12 (Block B)</p>
        <p>Singapore 512907</p>
      </div>
      <p class="contact-line">+65 6100 2040
        <svg viewBox="0 0 24 24" aria-label="Telephone"><path d="M6.6 10.8a15 15 0 0 0 6.6 6.6l2.2-2.2c.3-.3.7-.4 1-.2 1.1.4 2.3.6 3.6.6.6 0 1 .4 1 1V20c0 .6-.4 1-1 1A17 17 0 0 1 3 4c0-.6.4-1 1-1h3.5c.6 0 1 .4 1 1 0 1.3.2 2.5.6 3.6.1.3 0 .7-.2 1z"/></svg></p>
      <p class="contact-line">+65 9100 2233
        <svg viewBox="0 0 24 24" aria-label="Mobile"><path d="M7 1h10a2 2 0 0 1 2 2v18a2 2 0 0 1-2 2H7a2 2 0 0 1-2-2V3a2 2 0 0 1 2-2zm0 3v14h10V4z"/></svg></p>
      <p class="contact-line">+65 6100 2041
        <svg viewBox="0 0 24 24" aria-label="Fax"><path d="M6 2h12v6H6zM3 9h18a1 1 0 0 1 1 1v8h-4v4H6v-4H2v-8a1 1 0 0 1 1-1zm5 7v4h8v-4z"/></svg></p>
      <p class="contact-line">sales@kelvane.example
        <svg viewBox="0 0 24 24" aria-label="Email"><path d="M2 5h20v14H2zm2 2v.5l8 5 8-5V7l-8 5z"/></svg></p>
      <p class="contact-line">www.kelvane.example
        <svg viewBox="0 0 24 24" aria-label="Website"><circle cx="12" cy="12" r="10"/><path d="M2 12h20M12 2c3 3 3 17 0 20M12 2c-3 3-3 17 0 20" stroke="#fff" stroke-width="1.5" fill="none"/></svg></p>
      <p class="contact-reg">UEN No 200299117K</p>
    </div>
  </section>

</main>
</body>
</html>
```